Vegan bakery needs business card

We need a business card design for my vegan bakery in Philadelphia Pa. We create amazing whole food plant based cuisine that is egg and dairy free. We use fruits, vegetables, healing herbs, nuts, natural sugars (date, turbinado, agave) and non bleached flours in our creations. Due to demand and interest in the Philadelphia area we created a late night vegan dessert delivery service named Bramble Vegan. We are the only business providing delicious vegan desserts delivered to your door at 1am!! We would like to see designs that use the color scheme in the logo. The final design should communicate the benefits of our products: dairy/egg free, plant based, healing herbs, amazing food.

```html
<!DOCTYPE html>
<html lang="en">
<head>
<meta charset="utf-8">
<title>Bramble Vegan – Business Card</title>
<link rel="stylesheet" href="https://fonts.googleapis.com/css2?family=Questrial&display=swap">
<style>
  :root {
    --backdrop: #dddcde;
    --card: #ffffff;
    --accent: #f0704a;
    --ink: #6b6b6b;
    --ink-soft: #8a8a8a;
    --shadow: rgba(0, 0, 0, 0.18);
  }
  * { box-sizing: border-box; margin: 0; padding: 0; }
  html, body {
    width: 1200px;
    height: 837px;
    overflow: hidden;
    background: var(--backdrop);
    font-family: "Questrial", "Century Gothic", sans-serif;
  }
  .stage {
    position: relative;
    width: 1200px;
    height: 837px;
    display: flex;
    align-items: center;
    justify-content: center;
    gap: 50px;
  }
  .card {
    position: relative;
    width: 530px;
    height: 303px;
    background: var(--card);
    box-shadow: 0 10px 26px var(--shadow);
    overflow: hidden;
  }

  /* Back side: contact details */
  .card-back .identity {
    position: absolute;
    top: 92px;
    left: 70px;
    text-align: right;
    width: 170px;
  }
  .identity .person-name {
    color: var(--accent);
    font-size: 22px;
    letter-spacing: 0.3px;
  }
  .identity .person-role {
    color: var(--ink);
    font-size: 13px;
    margin-top: 4px;
  }
  .card-back .divider {
    position: absolute;
    top: 88px;
    left: 262px;
    width: 1.5px;
    height: 62px;
    background: var(--accent);
  }
  .card-back .contacts {
    position: absolute;
    top: 96px;
    left: 284px;
    list-style: none;
    color: var(--ink);
    font-size: 13px;
  }
  .contacts li {
    display: flex;
    align-items: center;
    gap: 8px;
    margin-bottom: 9px;
  }
  .contacts svg { width: 14px; height: 14px; flex: none; }
  .card-back .products {
    position: absolute;
    left: 0;
    right: 0;
    top: 196px;
    text-align: center;
  }
  .products .products-title {
    color: var(--accent);
    font-size: 13px;
    letter-spacing: 0.5px;
    margin-bottom: 8px;
  }
  .products .products-list {
    color: var(--ink);
    font-size: 14px;
  }

  /* Front side: brand and photo */
  .card-front .brand {
    position: absolute;
    top: 34px;
    left: 148px;
    display: flex;
    align-items: center;
    gap: 10px;
    color: var(--accent);
    font-size: 26px;
  }
  .brand .brand-dot {
    width: 14px;
    height: 14px;
    border-radius: 50%;
    background: var(--accent);
  }
  .card-front .photo {
    position: absolute;
    left: 0;
    bottom: 0;
    width: 530px;
    height: 200px;
  }
</style>
</head>
<body>
<main class="stage">
  <section class="card card-back" aria-label="Business card back">
    <div class="identity">
      <p class="person-name">Jordan Ellis</p>
      <p class="person-role">Director of Marketing</p>
    </div>
    <span class="divider"></span>
    <ul class="contacts">
      <li>
        <svg viewBox="0 0 14 14" aria-hidden="true">
          <circle cx="7" cy="7" r="6.3" fill="none" stroke="#f0704a" stroke-width="1.2"/>
          <path d="M4.6 4.2c.4-.4.9-.3 1.1.1l.5.9c.2.4 0 .7-.3.9-.2.2 0 .7.6 1.3.6.6 1.1.8 1.3.6.2-.3.5-.5.9-.3l.9.5c.4.2.5.7.1 1.1-.8.8-2.3.5-3.8-1S3.8 5 4.6 4.2z" fill="#f0704a"/>
        </svg>
        215-555-0148
      </li>
      <li>
        <svg viewBox="0 0 14 14" aria-hidden="true">
          <circle cx="7" cy="7" r="6.3" fill="none" stroke="#f0704a" stroke-width="1.2"/>
          <rect x="3.8" y="4.8" width="6.4" height="4.4" fill="none" stroke="#f0704a" stroke-width="1"/>
          <path d="M3.8 4.8 7 7.3l3.2-2.5" fill="none" stroke="#f0704a" stroke-width="1"/>
        </svg>
        hello@bramblevegan.com
      </li>
    </ul>
    <div class="products">
      <p class="products-title">OUR PRODUCTS</p>
      <p class="products-list">dairy/egg free | plant based | healing herbs | amazing food.</p>
    </div>
  </section>

  <section class="card card-front" aria-label="Business card front">
    <div class="brand">
      <span class="brand-dot"></span>
      <span class="brand-name">Bramble Vegan</span>
    </div>
    <svg class="photo" viewBox="0 0 530 200" preserveAspectRatio="none" role="img" aria-label="Photo of a heap of fresh fruits and vegetables beside a smiling woman in sportswear holding an apple">
      <defs>
        <linearGradient id="produce-tones" x1="0" y1="0" x2="1" y2="0">
          <stop offset="0" stop-color="#8a9a3c"/>
          <stop offset="0.2" stop-color="#e8a23a"/>
          <stop offset="0.38" stop-color="#d9472f"/>
          <stop offset="0.52" stop-color="#7fb548"/>
          <stop offset="0.66" stop-color="#3a3234"/>
          <stop offset="0.82" stop-color="#e9c6b4"/>
          <stop offset="1" stop-color="#ffffff"/>
        </linearGradient>
      </defs>
      <rect width="530" height="200" fill="url(#produce-tones)"/>
    </svg>
  </section>
</main>
</body>
</html>
```